We need a card and logo design for a new business based in Dallas Texas called Stonemarsh Financial LLC.

We provide bridge loans.We offer pay day loans,title loans and check cashing.Our products are emmergency loans that help borrowers meet short term liquidity needs until the next pay check.

The final design should communicate,professionalism,Sophistication and friendliness to our customers.Use the color Blue as much as possible and another eye catching color if possible.We will consider a profesional looking knight logo with the color Blue in it.Please design a full corporate identity.

```html
<!DOCTYPE html>
<html lang="en">
<head>
<meta charset="utf-8">
<title>Stonemarsh Financial LLC – Business Card</title>
<link rel="stylesheet" href="https://fonts.googleapis.com/css2?family=Montserrat:wght@700&display=swap">
<style>
  :root {
    --backdrop: #ececec;
    --card-dark: #3b3b3b;
    --card-white: #ffffff;
    --card-grey: #d3d3d3;
    --brand-blue: #1f6fc2;
    --brand-navy: #1d2466;
  }
  html, body {
    margin: 0;
    padding: 0;
    overflow: hidden;
  }
  .canvas {
    width: 1200px;
    height: 720px;
    background: var(--backdrop);
    display: flex;
    align-items: center;
    justify-content: center;
  }
  .business-card {
    position: relative;
    width: 340px;
    height: 595px;
    box-shadow: 0 10px 30px rgba(0, 0, 0, 0.25);
  }
  .card-shapes {
    position: absolute;
    inset: 0;
    display: block;
  }
  .card-shapes .band { fill: var(--card-dark); }
  .card-shapes .stripe { fill: var(--card-white); }
  .card-shapes .panel { fill: var(--card-grey); }
  .brand-lockup {
    position: absolute;
    left: 0;
    right: 0;
    top: 268px;
    display: flex;
    align-items: center;
    justify-content: center;
    gap: 12px;
  }
  .brand-dot {
    width: 44px;
    height: 44px;
    border-radius: 50%;
    background: var(--brand-navy);
    flex: none;
  }
  .brand-name {
    font-family: 'Montserrat', sans-serif;
    font-weight: 700;
    color: var(--brand-blue);
    line-height: 1;
  }
  .brand-name .primary {
    display: block;
    font-size: 29px;
    letter-spacing: 0.5px;
  }
  .brand-name .secondary {
    display: block;
    font-size: 13px;
    letter-spacing: 5.4px;
    margin-top: 5px;
  }
</style>
</head>
<body>
  <main class="canvas">
    <article class="business-card">
      <svg class="card-shapes" viewBox="0 0 340 595" width="340" height="595" aria-hidden="true">
        <rect class="band" x="0" y="0" width="340" height="595"/>
        <path class="stripe" d="M0,95 Q160,18 340,48 V545 Q180,580 0,508 Z"/>
        <path class="panel" d="M0,118 Q160,46 340,74 V522 Q180,552 0,490 Z"/>
      </svg>
      <div class="brand-lockup">
        <span class="brand-dot"></span>
        <h1 class="brand-name">
          <span class="primary">STONEMARSH</span>
          <span class="secondary">FINANCIAL LLC</span>
        </h1>
      </div>
    </article>
  </main>
</body>
</html>
```